Brivora Distance Learning Website

Brivora provide e-learning and mixed learning solutions for individuals, colleges, organisations and B2B.
We need a modern, light and flat website design for Brivora. We want to to see the designer incorporate user experience(UX) design elements into the AI or PSD mockups. We would like to see designs that use pastel colors that compliment yellow and black of our logo.
We want our E-learning experience to accelerate learning and for the interface to be user friendly and intuitive. We want the designs to focus on quick access to course information, course reviews, learning progress and study advice. Quick and intuitive access to all content for our clients is one of our top priorities.
We would like designs for the following project 3 pages:
1. Learner homepage dashboard (see attached screenshot).
On this page the Learners need to:
- Login
- Have quick access to Packages and Courses.
- See other recommended courses (Below Packages and Courses)
- Possibly a left hand side column/menu with thumbnail icons (See lumeqa learner dashboard screenshot)
2. Homepage
See current sample
http://www.brivora-learn.example
We would like the designer to focus on creating a customized banner to enhance the home page.
3. Primary Landing/Marketing page
This page is geared towards customer acquisition with the focal point being the top banner (video or HD image).
And Course Preview content below.
See reference
http://brivora-learn.example/subscriptionPlans/marketing/MTc%3D/Mjc4Nw%3D%3D/Speaking%20Nepali%20%2B%20Nepali%20Snacks%20Bundle%20by%20Lorne%20Pike%20Vell
Other site we like:
- https://www.skillorva.example (We like the home page and top bar on courses page)
- http://www.tutorcrest.example
- http://pixelgrovelab.example (think this site looks great, love the lower graphics on the homepage)
Updates
Hello,
Thank you for taking the time to contribute to this web design competition. We would just like to point out a few things:
1. Please try to make the color palette similar to the colors used in the screenshot that we just uploaded ('possible color palette).
2. Please make the designs specific to each page: THE LEARNER HOMEPAGE, HOME PAGE, and the MARKETING LANDING PAGE.
We are very happy with the high quality of designs so far,
Cheers,
Ned Ru
VK-Studio
Also,
Please avoid using dark/bold elements in the designs. The ONLY elements that we want to be dark are the logo and the footer.
Any questions please ask,
Cheers,
Ned Ru
Vk-Studio
Hello,
Based on the round of feedback we just gave it would be great if you could complete further design changes by tomorrow, as we are pushed for time.
Thank you,
Ned Ru
VK-Studio

```html
<!DOCTYPE html>
<html lang="en">
<head>
<meta charset="utf-8">
<title>Brivora – Learner Home</title>
<link href="https://fonts.googleapis.com/css2?family=Open+Sans:wght@300;400;600;700&display=swap" rel="stylesheet">
<style>
:root{
  --orange:#f7941d;
  --ink:#333333;
  --muted:#8a8a8a;
  --line:#e4e4e4;
  --sidebar:#2f2f2f;
  --sidebar-line:#3d3d3d;
  --bg:#ffffff;
  --kova:#e8780e;
  --pyrel:#2a6aa3;
  --tabulix:#1f7446;
  --footer:#fafafa;
  --social-red:#c0392b;
  --social-blue:#2f5f9e;
}
*{box-sizing:border-box;margin:0;padding:0}
html,body{width:1200px;height:3640px;overflow:hidden}
body{font-family:"Open Sans",Arial,sans-serif;color:var(--ink);background:var(--bg);position:relative}
a{color:inherit;text-decoration:none}

/* Hero */
.hero{position:absolute;left:0;top:0;width:1200px;height:640px;
  background:linear-gradient(180deg,#3b3a38 0%,#56514a 45%,#2a2826 100%)}
.hero-photo{position:absolute;left:110px;top:70px;right:0;bottom:0;
  background:radial-gradient(ellipse at 60% 40%,rgba(170,150,120,.35),rgba(0,0,0,0) 65%)}
.topbar{position:absolute;left:110px;right:0;top:0;height:70px;display:flex;align-items:center;padding:0 30px;background:rgba(0,0,0,.35)}
.brand{color:#fff;font-weight:700;font-size:26px;display:flex;align-items:center;gap:10px}
.brand-dot{width:14px;height:14px;background:var(--orange);border-radius:50%}
.nav{display:flex;gap:34px;margin-left:150px;color:#fff;font-size:12px;font-weight:700;letter-spacing:.5px}
.login{margin-left:auto;border:1px solid rgba(255,255,255,.7);color:#fff;font-size:12px;font-weight:600;padding:7px 16px;border-radius:2px}

.sidebar{position:absolute;left:0;top:0;width:110px;height:640px;background:var(--sidebar)}
.side-item{height:90px;border-bottom:1px solid var(--sidebar-line);display:flex;flex-direction:column;align-items:center;justify-content:center;gap:8px;color:#b5b5b5;font-size:9px;font-weight:600;text-transform:uppercase;text-align:center;line-height:1.25;padding:0 8px}
.side-item.active{background:var(--orange);color:#fff}
.side-item svg{width:26px;height:26px}

.hero-copy{position:absolute;left:330px;top:440px;width:700px;text-align:center;color:#fff}
.hero-copy h1{font-weight:400;font-size:26px;margin-bottom:18px}
.search{display:flex;height:40px;background:#fff;border-radius:2px;overflow:hidden}
.search span{flex:1;text-align:left;padding:0 16px;line-height:40px;color:#999;font-size:13px}
.search b{width:110px;background:var(--orange);line-height:40px;font-size:13px;font-weight:600;display:flex;align-items:center;justify-content:center;gap:6px}
.hero-copy p{font-size:12px;text-align:left;margin-top:12px;color:#ddd}

/* Intro */
.intro{position:absolute;left:150px;width:900px;top:700px;text-align:center;font-size:30px;font-weight:300;line-height:1.35;color:#444}

.topic{position:absolute;left:0;width:1200px;height:260px}
.topic .disc{position:absolute;width:230px;height:230px;border-radius:50%;display:flex;align-items:center;justify-content:center;color:#fff;font-size:38px;font-weight:600}
.topic .copy{position:absolute;width:440px}
.topic h2{font-size:30px;font-weight:400;color:#333;margin-bottom:16px}
.topic p{font-size:13px;line-height:1.75;color:#7d7d7d}
.kova{top:820px}.kova .disc{left:220px;top:0;background:var(--kova)}.kova .copy{left:530px;top:22px}
.pyrel{top:1100px}.pyrel .disc{left:750px;top:0;background:var(--pyrel)}.pyrel .copy{left:220px;top:10px}
.tabulix{top:1380px}.tabulix .disc{left:220px;top:0;background:var(--tabulix)}.tabulix .copy{left:530px;top:22px}

/* Banner */
.banner{position:absolute;left:0;top:1700px;width:1200px;height:400px;background:linear-gradient(90deg,#4a4642 0%,#7d7670 55%,#a59d94 100%)}
.banner-copy{position:absolute;left:100px;top:150px;color:#fff}
.banner-copy h3{font-size:30px;font-weight:600}
.banner-copy p{font-size:30px;font-weight:300;color:var(--orange);margin-top:2px}
.btn-orange{display:inline-block;margin-top:22px;background:var(--orange);color:#fff;font-size:14px;padding:10px 28px;border-radius:2px}

/* Courses */
.section-title{position:absolute;left:0;width:1200px;text-align:center;font-size:30px;font-weight:400;color:#444}
.recommended-title{top:2150px}
.course-grid{position:absolute;left:100px;top:2225px;width:1000px;display:grid;grid-template-columns:repeat(4,235px);gap:26px 20px}
.card{height:300px;border:1px solid var(--line);background:#fff;box-shadow:0 1px 3px rgba(0,0,0,.08)}
.card .thumb{height:155px}
.card h4{font-size:14px;font-weight:400;line-height:1.35;padding:12px 12px 4px;color:#444}
.card .by{font-size:11px;color:var(--muted);padding:0 12px}
.card .meta{display:flex;align-items:center;justify-content:space-between;border-top:1px solid var(--line);margin-top:14px;padding:10px 12px;font-size:11px;color:var(--muted)}
.card .meta span{display:flex;align-items:center;gap:6px}
.card .price{color:var(--orange);font-size:20px;font-weight:700}

.browse{position:absolute;left:480px;top:2900px;width:240px;height:44px;background:#555;color:#fff;text-align:center;line-height:44px;font-size:14px;border-radius:2px}

/* Features */
.features-title{top:3010px}
.features{position:absolute;left:200px;top:3085px;width:800px;display:grid;grid-template-columns:repeat(3,1fr);gap:20px}
.features h5{color:var(--orange);font-size:17px;font-weight:700;margin-bottom:10px}
.features ul{list-style:none;font-size:12px;line-height:1.75;color:#666}
.features .apps{margin-top:24px}

/* Footer */
.footer{position:absolute;left:0;top:3470px;width:1200px;height:170px;background:var(--footer);border-top:1px solid var(--line);text-align:center}
.footer small{display:block;margin-top:18px;font-size:11px;color:var(--muted)}
.footer-brand{display:inline-flex;align-items:center;gap:8px;margin-top:14px;background:#222;color:#fff;font-weight:700;font-size:22px;padding:8px 18px}
.footer-brand i{width:12px;height:12px;background:var(--orange);border-radius:50%}
.social{display:flex;justify-content:center;gap:10px;margin-top:14px}
.social i{width:26px;height:26px;border-radius:50%;background:var(--social-blue)}
.social i:first-child,.social i:last-child{background:var(--social-red)}
</style>
</head>
<body>

<header class="hero">
  <div class="hero-photo" role="img" aria-label="Photo of a learner studying at a desk"></div>
  <div class="topbar">
    <a class="brand"><span class="brand-dot"></span>Brivora</a>
    <nav class="nav"><a>STORE</a><a>SUBSCRIBED LEARNING PACKAGES</a><a>MY PUBLISHING PACKAGES</a><a>BOOKMARKS</a></nav>
    <a class="login">LOGIN ▾</a>
  </div>
  <aside class="sidebar">
    <div class="side-item active">
      <svg viewBox="0 0 24 24" fill="none" stroke="#fff" stroke-width="2"><path d="M3 11l9-8 9 8v10h-6v-6H9v6H3z"/></svg>Dashboard</div>
    <div class="side-item">
      <svg viewBox="0 0 24 24" fill="none" stroke="#b5b5b5" stroke-width="2"><rect x="3" y="3" width="7" height="7"/><rect x="14" y="3" width="7" height="7"/><rect x="3" y="14" width="7" height="7"/><rect x="14" y="14" width="7" height="7"/></svg>Platform Overview</div>
    <div class="side-item">
      <svg viewBox="0 0 24 24" fill="none" stroke="#b5b5b5" stroke-width="2"><circle cx="10" cy="10" r="6"/><path d="M15 15l6 6"/></svg>Find Learning Packages</div>
    <div class="side-item">
      <svg viewBox="0 0 24 24" fill="none" stroke="#b5b5b5" stroke-width="2"><path d="M3 5h18v11H8l-5 4z"/></svg>Interacting Channels</div>
    <div class="side-item">
      <svg viewBox="0 0 24 24" fill="none" stroke="#b5b5b5" stroke-width="2"><path d="M6 2h9l5 5v15H6z"/><path d="M9 12h8M9 16h8"/></svg>Training History</div>
    <div class="side-item">
      <svg viewBox="0 0 24 24" fill="none" stroke="#b5b5b5" stroke-width="2"><circle cx="12" cy="12" r="3"/><circle cx="12" cy="12" r="8" stroke-dasharray="3 3"/></svg>Settings</div>
    <div class="side-item">
      <svg viewBox="0 0 24 24" fill="none" stroke="#b5b5b5" stroke-width="2"><path d="M12 3l2.7 5.6 6.1.9-4.4 4.3 1 6.1L12 17l-5.4 2.9 1-6.1-4.4-4.3 6.1-.9z"/></svg>Preferences</div>
  </aside>
  <div class="hero-copy">
    <h1>Your place to learn real world skills online</h1>
    <div class="search"><span>What do you want to learn today?</span><b>
      <svg width="13" height="13" viewBox="0 0 24 24" fill="none" stroke="#fff" stroke-width="3"><circle cx="10" cy="10" r="6"/><path d="M15 15l6 6"/></svg>Search</b></div>
    <p>Search for online courses on Web development, Yoga, Guitar lessons, or anything else</p>
  </div>
</header>

<p class="intro">Brivora provide e-learning and mixed learning solutions for individuals, colleges, organisations and B2B.</p>

<section class="topic kova">
  <div class="disc">Kova</div>
  <div class="copy"><h2>Top Kova courses</h2>
    <p>Lorem Ipsum is simply dummy text of the printing and typesetting industry. Lorem Ipsum has been the industry's standard dummy text ever since the 1500s, when an unknown printer took a galley of type and scrambled it to make a type specimen book. It has survived not only five centuries, but also the leap into electronic typesetting, remaining essentially...</p></div>
</section>

<section class="topic pyrel">
  <div class="disc">Pyrel</div>
  <div class="copy"><h2>Top Pyrel courses</h2>
    <p>Lorem Ipsum is simply dummy text of the printing and typesetting industry. Lorem Ipsum has been the industry's standard dummy text ever since the 1500s, when an unknown printer took a galley of type and scrambled it to make a type specimen book. It has survived not only five centuries, but also the leap into electronic typesetting, remaining essentially...</p></div>
</section>

<section class="topic tabulix">
  <div class="disc">Tabulix</div>
  <div class="copy"><h2>Top Tabulix courses</h2>
    <p>Lorem Ipsum is simply dummy text of the printing and typesetting industry. Lorem Ipsum has been the industry's standard dummy text ever since the 1500s, when an unknown printer took a galley of type and scrambled it to make a type specimen book. It has survived not only five centuries, but also the leap into electronic typesetting, remaining essentially...</p></div>
</section>

<section class="banner" role="img" aria-label="Photo of a student working on a laptop in a study room">
  <div class="banner-copy">
    <h3>Quick access to Packages and Courses</h3>
    <p>Take your career to the next level</p>
    <a class="btn-orange">Sign up</a>
  </div>
</section>

<h2 class="section-title recommended-title">See other recommended courses</h2>
<div class="course-grid">
  <article class="card"><div class="thumb" role="img" aria-label="Programming book cover" style="background:linear-gradient(135deg,#3a3a3a,#7a7a7a)"></div><h4>RankWise Search Engine Optimisation Training</h4><div class="by">By Dale Morren</div><div class="meta"><span><svg width="14" height="14" viewBox="0 0 24 24" fill="#aaa"><circle cx="12" cy="8" r="4"/><path d="M4 21c0-5 16-5 16 0z"/></svg>138 Enrolled</span><span class="price">$487</span></div></article>
  <article class="card"><div class="thumb" role="img" aria-label="Office suite box artwork" style="background:linear-gradient(135deg,#d8e84a,#f0a640)"></div><h4>RankWise Search Engine Optimisation Training</h4><div class="by">By Dale Morren</div><div class="meta"><span><svg width="14" height="14" viewBox="0 0 24 24" fill="#aaa"><circle cx="12" cy="8" r="4"/><path d="M4 21c0-5 16-5 16 0z"/></svg>138 Enrolled</span><span class="price">$487</span></div></article>
  <article class="card"><div class="thumb" role="img" aria-label="Coffee cup on a desk" style="background:linear-gradient(135deg,#efefef,#8a8a8a)"></div><h4>RankWise Search Engine Optimisation Training</h4><div class="by">By Dale Morren</div><div class="meta"><span><svg width="14" height="14" viewBox="0 0 24 24" fill="#aaa"><circle cx="12" cy="8" r="4"/><path d="M4 21c0-5 16-5 16 0z"/></svg>138 Enrolled</span><span class="price">$487</span></div></article>
  <article class="card"><div class="thumb" role="img" aria-label="Person working on a laptop" style="background:linear-gradient(135deg,#c9c5bf,#6e6a66)"></div><h4>RankWise Search Engine Optimisation Training</h4><div class="by">By Dale Morren</div><div class="meta"><span><svg width="14" height="14" viewBox="0 0 24 24" fill="#aaa"><circle cx="12" cy="8" r="4"/><path d="M4 21c0-5 16-5 16 0z"/></svg>138 Enrolled</span><span class="price">$487</span></div></article>
  <article class="card"><div class="thumb" role="img" aria-label="Student with a tablet" style="background:linear-gradient(135deg,#3b4e6e,#b08a6a)"></div><h4>RankWise Search Engine Optimisation Training</h4><div class="by">By Dale Morren</div><div class="meta"><span><svg width="14" height="14" viewBox="0 0 24 24" fill="#aaa"><circle cx="12" cy="8" r="4"/><path d="M4 21c0-5 16-5 16 0z"/></svg>138 Enrolled</span><span class="price">$487</span></div></article>
  <article class="card"><div class="thumb" role="img" aria-label="Open books on a shelf" style="background:linear-gradient(135deg,#8a5a2c,#e0c080)"></div><h4>RankWise Search Engine Optimisation Training</h4><div class="by">By Dale Morren</div><div class="meta"><span><svg width="14" height="14" viewBox="0 0 24 24" fill="#aaa"><circle cx="12" cy="8" r="4"/><path d="M4 21c0-5 16-5 16 0z"/></svg>138 Enrolled</span><span class="price">$487</span></div></article>
  <article class="card"><div class="thumb" role="img" aria-label="Student writing notes" style="background:linear-gradient(135deg,#c8c2b8,#5c5650)"></div><h4>RankWise Search Engine Optimisation Training</h4><div class="by">By Dale Morren</div><div class="meta"><span><svg width="14" height="14" viewBox="0 0 24 24" fill="#aaa"><circle cx="12" cy="8" r="4"/><path d="M4 21c0-5 16-5 16 0z"/></svg>138 Enrolled</span><span class="price">$487</span></div></article>
  <article class="card"><div class="thumb" role="img" aria-label="Spreadsheet application artwork" style="background:linear-gradient(135deg,#e9f2ea,#4e9a63)"></div><h4>RankWise Search Engine Optimisation Training</h4><div class="by">By Dale Morren</div><div class="meta"><span><svg width="14" height="14" viewBox="0 0 24 24" fill="#aaa"><circle cx="12" cy="8" r="4"/><path d="M4 21c0-5 16-5 16 0z"/></svg>138 Enrolled</span><span class="price">$487</span></div></article>
</div>
<a class="browse">Browse Courses</a>

<h2 class="section-title features-title">Brivora Features</h2>
<div class="features">
  <div><h5>Learning</h5><ul><li>Expert Teachers</li><li>Tracks</li><li>Library</li><li>Forum</li><li>Workspaces</li><li>Video</li><li>Stages</li><li>Code Challenges</li><li>Quizzes</li><li>Conferences</li><li>Bonus Lessons</li><li>Live Workshops</li></ul></div>
  <div><h5>Topics</h5><ul><li>HTML</li><li>CSS</li><li>Rubel</li><li>ScriptLang</li><li>Hypr</li><li>Design</li><li>PressKit</li><li>Orbit OS</li><li>Droidal</li><li>Pyrel</li><li>Development Tools</li><li>Business</li></ul></div>
  <div><h5>Student Account</h5><ul><li>Activity Feed</li><li>Profile</li><li>Notifications</li><li>Points</li><li>Badges</li><li>Groups</li><li>Student Perks</li></ul>
    <h5 class="apps">Native Apps</h5><ul><li>Tablet App</li><li>Droidal App</li></ul></div>
</div>

<footer class="footer">
  <small>©2015 Brivora. Terms • Privacy • Contact</small>
  <div class="footer-brand"><i></i>Brivora</div>
  <div class="social"><i></i><i></i><i></i><i></i><i></i></div>
</footer>

</body>
</html>
```